Website Design for The Elder Nook

Please design and code a new website.
Here are the sites I like best:
http://www.voyaglint.com/alternate/
http://www.wheelgiftbay.org
Please make it similar but look at the competitor site (below) for images and wording. This is NOT a car donation site. It's a senior lead placement site like https://www.kinhavenfinder.com. I just like this sites above as a lead generation sites.
Competitor site:
https://www.kinhavenfinder.com (use ideas / verbiage from this site)
Updates
Competitor site:
Coding
Coded - Design and coding required
Number of Pages Required
1 page
Look and feel
Each slider illustrates characteristics of the customer's brand and the style your logo design should communicate.

```html
<!DOCTYPE html>
<html lang="en">
<head>
<meta charset="utf-8">
<title>The Elder Nook</title>
<link href="https://fonts.googleapis.com/css2?family=Noto+Serif:ital,wght@0,400;0,700;1,400&family=Jost:wght@300;400;500&display=swap" rel="stylesheet">
<style>
:root{
  --blue:#0d5bb0;
  --blue-dark:#0a4b94;
  --green:#8cc63f;
  --green-dark:#78b22e;
  --ink:#2b2b2b;
  --muted:#6d6d6d;
  --line:#e2e2e2;
  --white:#fff;
  --serif:"Noto Serif",Georgia,serif;
  --sans:"Jost",Arial,sans-serif;
}
*{box-sizing:border-box;margin:0;padding:0}
html,body{width:1200px;height:3040px;overflow:hidden}
body{font-family:var(--sans);color:var(--ink);background:var(--white);position:relative}
.wrap{position:relative;width:918px;margin:0 auto}
section,header,nav,footer{position:absolute;left:0;width:1200px}

/* header */
.site-header{top:0;height:91px}
.brand{position:absolute;left:142px;top:26px;display:flex;align-items:center;gap:10px;font-family:var(--serif);font-size:24px;color:var(--green-dark)}
.brand-dot{width:30px;height:30px;border-radius:50%;background:var(--green)}
.call{position:absolute;left:573px;top:22px;display:flex;gap:10px;align-items:center}
.call small{display:block;font-family:var(--serif);font-size:11px;color:#444}
.call strong{display:block;font-weight:400;font-size:24px;color:#222;line-height:1.1}
.badge{position:absolute;left:805px;top:22px;width:127px;height:48px;border-radius:4px;background:#1a4f86}
.lang{position:absolute;left:957px;top:28px;width:102px;height:34px;border:1px solid var(--line);display:flex;align-items:center;padding-left:12px;gap:8px;font-size:13px;color:#555}
.flag{width:34px;height:18px;background:linear-gradient(#b22234 0 50%,#e8e8e8 50%);position:relative}
.flag::before{content:"";position:absolute;left:0;top:0;width:15px;height:10px;background:#3c3b6e}

/* nav */
.main-nav{top:91px;height:43px;background:var(--blue)}
.main-nav ul{list-style:none;display:flex;position:absolute;left:142px;top:0;height:43px}
.main-nav li{font-family:var(--serif);font-size:12.5px;color:var(--white);padding:0 11px;line-height:43px;border-right:1px solid rgba(255,255,255,.18);text-transform:uppercase}
.main-nav li.active{background:var(--blue-dark);border-bottom:3px solid #0b3f7c}

/* hero */
.hero{top:134px;height:573px;background:linear-gradient(120deg,#7d9a55 0%,#a8b870 30%,#5e7d3a 60%,#8aa05a 100%)}
.hero-photo{position:absolute;inset:0}
.inquiry{position:absolute;left:694px;top:45px;width:365px;height:418px;background:rgba(235,240,228,.55)}
.inquiry h2{height:63px;background:var(--green);color:var(--white);font-family:var(--serif);font-weight:400;font-size:25px;text-align:center;line-height:63px}
.field{position:absolute;left:29px;width:306px;height:42px;background:var(--white);border:1px solid #ddd;display:flex}
.field .ic{width:40px;border-right:1px solid #ddd;background:#f5f5f5;display:flex;align-items:flex-start;justify-content:center;padding-top:13px}
.field span{padding:13px 16px;font-size:13px;color:#666}
.submit{position:absolute;left:29px;top:342px;width:306px;height:38px;background:var(--blue);color:var(--white);font-family:var(--serif);font-size:15px;text-align:center;line-height:38px}
.hero-line{position:absolute;left:0;width:1200px;top:502px;text-align:center;font-family:var(--serif);font-size:32px;color:var(--white);text-shadow:0 2px 4px rgba(0,0,0,.4)}

/* support */
.support{top:707px;height:544px}
.sec-title{font-family:var(--serif);font-weight:400;color:var(--blue);text-align:center;font-size:29px}
.support .sec-title{position:absolute;top:74px;width:100%}
.lead{position:absolute;top:122px;left:200px;width:800px;text-align:center;font-size:14.5px;line-height:24px;color:#333}
.cards{position:absolute;top:193px;left:142px;display:flex;gap:14px}
.card{width:172px;height:180px;border:1px solid var(--line);box-shadow:0 3px 6px rgba(0,0,0,.08);text-align:center;padding-top:24px;font-size:18px;line-height:21px;color:#333;font-weight:300}
.card svg{display:block;margin:0 auto 10px}
.nocost{position:absolute;top:425px;left:142px;width:918px;display:flex;align-items:center}
.nocost h3{font-family:var(--serif);font-weight:400;font-size:25px;color:var(--green-dark);width:284px}
.nocost h3 b{font-weight:400;color:var(--blue)}
.nocost p{font-size:17px;line-height:24px;color:#333;font-weight:300;width:445px}
.nocost a{font-size:21px;color:var(--blue);text-decoration:none;margin-left:auto;margin-right:8px}

/* advisor */
.advisor{top:1251px;height:480px;background:linear-gradient(90deg,#1c5fae,#2b6ec0 50%,#1b5ba8);color:var(--white)}
.advisor-photo{position:absolute;inset:0}
.advisor .sec-title{position:absolute;top:78px;width:100%;color:var(--white)}
.advisor .sub{position:absolute;top:126px;width:100%;text-align:center;font-size:15px}
.points{position:absolute;top:174px;left:236px;display:flex;gap:40px}
.point{width:220px;text-align:center;font-size:16px;line-height:20px}
.point .ring{width:98px;height:98px;border:1.5px solid var(--white);border-radius:50%;margin:0 auto 14px;display:flex;align-items:center;justify-content:center}
.search{position:absolute;top:350px;left:298px;width:604px;height:45px;background:var(--white);display:flex;align-items:center;padding:3px}
.search span{flex:1;padding-left:18px;color:#333;font-size:15px}
.search b{width:222px;height:37px;background:var(--green);font-family:var(--serif);font-weight:400;font-size:15px;text-align:center;line-height:37px}

/* testimonials */
.testimonials{top:1731px;height:484px}
.testimonials .sec-title{position:absolute;top:79px;width:100%}
.quotes{position:absolute;top:139px;left:142px;display:flex;gap:32px}
.quote{width:284px;position:relative;height:220px}
.quote p{height:146px;border:1px solid var(--line);padding:14px 17px;font-size:13px;line-height:21.5px;color:#777;letter-spacing:.3px}
.quote .who{position:absolute;top:128px;left:8px;display:flex;align-items:center;gap:20px;font-family:var(--serif);font-size:14px;color:#333}
.avatar{width:70px;height:70px;border-radius:50%;border:3px solid var(--blue);background:radial-gradient(circle at 50% 45%,#d9b79b,#8a6a55)}
.btn{display:block;background:var(--green);color:var(--white);font-family:var(--serif);font-size:15px;text-align:center;line-height:38px;height:38px}
.testimonials .btn{position:absolute;top:362px;left:496px;width:208px}

/* veteran */
.veteran{top:2215px;height:291px;background:linear-gradient(180deg,#233048 0%,#3a3e4c 40%,#6a2226 75%,#3b0f12 100%);color:var(--white);text-align:center}
.veteran-photo{position:absolute;inset:0}
.veteran h2{position:absolute;top:72px;width:100%;font-family:var(--serif);font-weight:400;font-size:25px}
.veteran p{position:absolute;top:113px;width:100%;font-size:14.5px;line-height:24px;font-weight:300}
.veteran .btn{position:absolute;top:176px;left:535px;width:130px}

/* states */
.states{top:2506px;height:366px}
.states .sec-title{position:absolute;top:80px;width:100%}
.cols{position:absolute;top:136px;left:159px;display:flex}
.cols ul{list-style:none;font-size:13px;line-height:21.8px;color:#333}
.cols li::before{content:"› "}

/* footer */
.site-footer{top:2872px;height:168px;background:var(--blue);color:var(--white)}
.foot-nav{position:absolute;top:48px;left:0;width:100%;display:flex;justify-content:center;gap:33px;list-style:none;font-family:var(--serif);font-size:11px;text-transform:uppercase}
.foot-rule{position:absolute;top:113px;left:142px;width:918px;border-top:1px solid rgba(255,255,255,.2)}
.copy{position:absolute;top:131px;left:142px;font-size:13px}
.social{position:absolute;top:128px;left:946px;display:flex;gap:6px}
.social i{width:24px;height:24px;border-radius:50%;border:1.5px solid var(--white);background:#1d6ac0}
</style>
</head>
<body>

<header class="site-header">
  <div class="brand"><span class="brand-dot"></span>The Elder Nook</div>
  <div class="call">
    <svg width="34" height="34" viewBox="0 0 24 24" fill="none" stroke="#0d5bb0" stroke-width="1.4"><path d="M5 3h4l2 5-2.5 1.5a11 11 0 0 0 6 6L16 13l5 2v4a2 2 0 0 1-2 2A16 16 0 0 1 3 5a2 2 0 0 1 2-2z"/></svg>
    <div><small>Talk to a local advisor for FREE</small><strong>(123) 456-7890</strong></div>
  </div>
  <div class="badge" role="img" aria-label="Accreditation badge"></div>
  <div class="lang">EN : <span class="flag"></span>
    <svg width="9" height="6" viewBox="0 0 9 6"><path d="M1 1l3.5 3.5L8 1" stroke="#555" fill="none"/></svg></div>
</header>

<nav class="main-nav">
  <ul>
    <li class="active">Assisted Living</li><li>Memory Care</li><li>Nursing Homes</li>
    <li>More Living Options ⌄</li><li>Planning &amp; Advice</li><li>How Our Service Works</li>
  </ul>
</nav>

<section class="hero">
  <div class="hero-photo" role="img" aria-label="Caregiver smiling beside an elderly man in a wheelchair outdoors among green foliage"></div>
  <form class="inquiry">
    <h2>Quick Inquiry</h2>
    <div class="field" style="top:91px"><div class="ic"><svg width="12" height="12" viewBox="0 0 12 12" fill="#444"><circle cx="6" cy="3.5" r="3"/><path d="M0 12a6 6 0 0 1 12 0z"/></svg></div><span>Name</span></div>
    <div class="field" style="top:144px"><div class="ic"><svg width="12" height="12" viewBox="0 0 24 24" fill="#444"><path d="M5 2h4l2 6-3 2a12 12 0 0 0 6 6l2-3 6 2v4a2 2 0 0 1-2 2A18 18 0 0 1 3 4a2 2 0 0 1 2-2z"/></svg></div><span>Phone</span></div>
    <div class="field" style="top:198px"><div class="ic"><svg width="12" height="10" viewBox="0 0 12 10" fill="#444"><rect width="12" height="10" rx="1"/><path d="M0 1l6 4 6-4" stroke="#f5f5f5" fill="none"/></svg></div><span>Email</span></div>
    <div class="field" style="top:252px;height:70px"><div class="ic"><svg width="14" height="12" viewBox="0 0 14 12" fill="#444"><ellipse cx="6" cy="5" rx="6" ry="4.5"/><path d="M2 8l-1 4 4-2z"/></svg></div><span>Message</span></div>
    <div class="submit">Submit Now</div>
  </form>
  <div class="hero-line">You know your family. We know <i>Senior Living.</i></div>
</section>

<section class="support">
  <h2 class="sec-title">The Support You Need To Make The Right Choice</h2>
  <p class="lead">Lorem ipsum dolor sit amet, consectetuer adipiscing elit, sed diam nonummy nibh euismod tincidunt ut laoreet dolore magna aliquam erat volutpat. Ut wisi enim ad minim veniam, quis nostrud exerci tation ullamcorper suscipit.</p>
  <div class="cards">
    <div class="card"><svg width="44" height="56" viewBox="0 0 44 56" fill="none" stroke="#78b22e" stroke-width="2"><circle cx="22" cy="14" r="9"/><path d="M4 55V38a10 10 0 0 1 10-10h16a10 10 0 0 1 10 10v17M22 28v27M17 28l5 8 5-8"/></svg>Dedicated local advisor</div>
    <div class="card"><svg width="50" height="56" viewBox="0 0 50 56" fill="none" stroke="#78b22e" stroke-width="2"><path d="M3 26L25 4l22 22M9 20v34h32V20M20 54V40h10v14"/><rect x="21" y="24" width="8" height="8"/></svg>Hand-picked list of communities to match your needs</div>
    <div class="card"><svg width="50" height="56" viewBox="0 0 50 56" fill="none" stroke="#78b22e" stroke-width="2"><circle cx="26" cy="22" r="10"/><path d="M26 16v12M23 19h5a2 2 0 0 1 0 4h-4a2 2 0 0 0 0 4h5M26 2v5M19 4l1 4M33 4l-1 4M3 40h8l10 4h10a3 3 0 0 1 0 6H19M11 40v14H3"/></svg>Full details and pricing</div>
    <div class="card"><svg width="52" height="56" viewBox="0 0 52 56" fill="none" stroke="#78b22e" stroke-width="2"><rect x="3" y="8" width="46" height="46"/><path d="M3 18h46M14 3v9M38 3v9M12 26h28v20H12zM12 33h28M12 40h28M19 26v20M26 26v20M33 26v20"/></svg>Help scheduling tours</div>
    <div class="card"><svg width="62" height="56" viewBox="0 0 62 56" fill="none" stroke="#78b22e" stroke-width="2"><path d="M10 8h30v30H10zM40 18h10l8 10v10H40M2 16h10M4 24h8M2 32h10"/><circle cx="18" cy="42" r="5"/><circle cx="48" cy="42" r="5"/></svg>Move in support</div>
  </div>
  <div class="nocost">
    <h3>There's <b>No Cost To You.</b></h3>
    <p>We work with over 20,000 senior living communities. Our community partners pay us for placement services.</p>
    <a href="tel:1234567890">Call (123) 456-7890</a>
  </div>
</section>

<section class="advisor">
  <div class="advisor-photo" role="img" aria-label="Row of portraits of local advisors under a blue tint"></div>
  <h2 class="sec-title">Your local advisor informs. You decide.</h2>
  <p class="sub">Lorem ipsum dolor sit amet, consectetuer adipiscing elit, sed diam nonummy nibh euismod tincidunt ut laoreet.</p>
  <div class="points">
    <div class="point"><div class="ring"><svg width="30" height="60" viewBox="0 0 30 60" fill="none" stroke="#fff" stroke-width="2"><circle cx="15" cy="14" r="11"/><circle cx="11" cy="11" r="3"/><path d="M15 25v33"/></svg></div>Insider's tips for the area near you</div>
    <div class="point"><div class="ring"><svg width="52" height="46" viewBox="0 0 52 46" fill="none" stroke="#fff" stroke-width="2.4"><path d="M26 44L5 23A12 12 0 0 1 26 8a12 12 0 0 1 21 15z"/></svg></div>Advice tailored to your unique situation</div>
    <div class="point"><div class="ring"><svg width="52" height="44" viewBox="0 0 52 44" fill="none" stroke="#fff" stroke-width="2"><circle cx="5" cy="6" r="4"/><circle cx="5" cy="22" r="4"/><circle cx="5" cy="38" r="4"/><path d="M16 6h34M16 22h34M16 38h34"/></svg></div>Time saving know-how and resources</div>
  </div>
  <div class="search"><span>Enter city or postal code</span><b>Find an advisor near you</b></div>
</section>

<section class="testimonials">
  <h2 class="sec-title">93% Of Our Customers Recommend Our Service</h2>
  <div class="quotes">
    <div class="quote"><p>Lorem ipsum dolor sit amet, consectetuer adipiscing elit, sed diam nonummy nibh euismod tincidunt ut laoreet dolore magna aliquam erat volutpat. Ut wisi enim ad minim veniam, quis nostrud.</p><div class="who"><span class="avatar" role="img" aria-label="Customer portrait"></span>Mara Lindqvist</div></div>
    <div class="quote"><p>Lorem ipsum dolor sit amet, consectetuer adipiscing elit, sed diam nonummy nibh euismod tincidunt ut laoreet dolore magna aliquam erat volutpat. Ut wisi enim ad minim veniam, quis nostrud.</p><div class="who"><span class="avatar" role="img" aria-label="Customer portrait"></span>Owen Teague</div></div>
    <div class="quote"><p>Lorem ipsum dolor sit amet, consectetuer adipiscing elit, sed diam nonummy nibh euismod tincidunt ut laoreet dolore magna aliquam erat volutpat. Ut wisi enim ad minim veniam, quis nostrud.</p><div class="who"><span class="avatar" role="img" aria-label="Customer portrait"></span>Nina Corvell</div></div>
  </div>
  <a class="btn">See More Testimonials</a>
</section>

<section class="veteran">
  <div class="veteran-photo" role="img" aria-label="Waving national flag in dark tones"></div>
  <h2>Access Up To $2,000 Per Month In Veteran's Aid</h2>
  <p>We work with Veterans every day. Most veteran families do not know of a key benefit available to them and their families.<br>It's called the Veteran's Aid and Attendance benefit. This benefit can help pay for senior living and home care.</p>
  <a class="btn">Learn More</a>
</section>

<section class="states">
  <h2 class="sec-title">Senior Assisted Living by State</h2>
  <div class="cols">
    <ul style="width:142px"><li>Alabama</li><li>Arizona</li><li>Arkansas</li><li>California</li><li>Colorado</li><li>Connecticut</li><li>Delaware</li></ul>
    <ul style="width:185px"><li>District of Columbia</li><li>Florida</li><li>Georgia</li><li>Hawaii</li><li>Idaho</li><li>Illinois</li><li>Indiana</li></ul>
    <ul style="width:158px"><li>Iowa</li><li>Kansas</li><li>Kentucky</li><li>Louisiana</li><li>Maine</li><li>Maryland</li><li>Massachusetts</li></ul>
    <ul style="width:136px"><li>Michigan</li><li>Minnesota</li><li>Mississippi</li><li>Missouri</li><li>Montana</li><li>Nebraska</li><li>Nevada</li></ul>
    <ul style="width:169px"><li>New Hampshire</li><li>New Jersey</li><li>New Mexico</li><li>New York</li><li>North Carolina</li><li>North Dakota</li><li>Ohio</li></ul>
    <ul><li>Oklahoma</li><li>Oregon</li><li>Pennsylvania</li><li>Rhode Island</li><li>South Carolina</li><li>South Dakota</li><li>Tennessee</li></ul>
  </div>
</section>

<footer class="site-footer">
  <ul class="foot-nav"><li>Assisted Living</li><li>Memory Care</li><li>Nursing Homes</li><li>More Living Options ⌄</li><li>Planning &amp; Advice</li><li>How Our Service Works</li></ul>
  <div class="foot-rule"></div>
  <p class="copy">Copyright 2019 The Elder Nook. All Rights Reserved.</p>
  <div class="social"><i></i><i></i><i></i><i></i></div>
</footer>

</body>
</html>
```